Custom Seed Packet design for Flower Farm

We need a design for our seeds packets.
The design will be a kind of "fill in the blanks" as we need the design to be adaptable for multiple varieties of seed. We will be using the design for a rubber stamp.
Our seed packets are 90x90mm in size.
Black logo only. No colour required.
A vintage botanical influence is desired.
Will need to include the following info,
"Wrenfield Gable Co logo" , "Seeds", "Plant Type", "Variety", "Harvested"

```html
<!DOCTYPE html>
<html lang="en">
<head>
<meta charset="utf-8">
<title>Wrenfield Gable Co – Seed Packet Stamp</title>
<link rel="stylesheet" href="https://fonts.googleapis.com/css2?family=Cormorant+Garamond:wght@500&family=Playball&family=Oswald:wght@300&display=swap">
<style>
  :root {
    --kraft: #d8c7a3;
    --ink: #141210;
    --ornament: #8f7d5f;
    --label-text: #e9dcc0;
  }
  * { box-sizing: border-box; margin: 0; padding: 0; }
  html, body { width: 1122px; height: 1200px; overflow: hidden; }
  body { background: var(--kraft); position: relative; }

  .stamp-frame {
    position: absolute;
    left: 61px; top: 105px;
    width: 1000px; height: 990px;
    border: 3px solid var(--ink);
  }
  .ornament {
    position: absolute;
    background: var(--ornament);
    opacity: 0.55;
    border-radius: 6px;
  }
  .ornament--corner { width: 175px; height: 225px; }
  .ornament--tl { left: 0; top: 0; }
  .ornament--tr { right: 0; top: 0; }
  .ornament--bl { left: 0; bottom: 0; }
  .ornament--br { right: 0; bottom: 0; }
  .ornament--edge { width: 342px; height: 63px; left: 329px; }
  .ornament--top { top: 0; }
  .ornament--bottom { bottom: 0; }

  .brand-name {
    position: absolute;
    left: 0; right: 0; top: 290px;
    text-align: center;
    font-family: "Cormorant Garamond", serif;
    font-weight: 500;
    font-size: 52px;
    color: var(--ink);
  }

  .packet-title {
    position: absolute;
    left: 0; right: 0; top: 420px;
    text-align: center;
    font-family: "Playball", cursive;
    font-size: 190px;
    line-height: 1;
    color: var(--ink);
  }

  .info-fields {
    position: absolute;
    left: 200px; top: 691px;
    width: 597px;
    list-style: none;
  }
  .info-field {
    display: flex;
    height: 38px;
    margin-bottom: 18px;
    border: 2px solid var(--ink);
    border-radius: 19px;
    overflow: hidden;
  }
  .info-field__label {
    width: 180px;
    background: var(--ink);
    color: var(--label-text);
    font-family: "Oswald", sans-serif;
    font-weight: 300;
    font-size: 24px;
    line-height: 34px;
    padding-left: 20px;
    white-space: nowrap;
  }
  .info-field__blank { flex: 1; }
</style>
</head>
<body>
  <main class="stamp-frame">
    <div class="ornament ornament--corner ornament--tl" role="img" aria-label="Black spiral scroll ornament, top left corner"></div>
    <div class="ornament ornament--edge ornament--top" role="img" aria-label="Black spiral scroll ornament, top centre"></div>
    <div class="ornament ornament--corner ornament--tr" role="img" aria-label="Black spiral scroll ornament, top right corner"></div>
    <div class="ornament ornament--corner ornament--bl" role="img" aria-label="Black spiral scroll ornament, bottom left corner"></div>
    <div class="ornament ornament--edge ornament--bottom" role="img" aria-label="Black spiral scroll ornament, bottom centre"></div>
    <div class="ornament ornament--corner ornament--br" role="img" aria-label="Black spiral scroll ornament, bottom right corner"></div>

    <p class="brand-name">Wrenfield Gable Co</p>

    <h1 class="packet-title">Seeds</h1>

    <ul class="info-fields">
      <li class="info-field"><span class="info-field__label">Seeds</span><span class="info-field__blank"></span></li>
      <li class="info-field"><span class="info-field__label">Plant Type</span><span class="info-field__blank"></span></li>
      <li class="info-field"><span class="info-field__label">Variety</span><span class="info-field__blank"></span></li>
      <li class="info-field"><span class="info-field__label">Harvested</span><span class="info-field__blank"></span></li>
    </ul>
  </main>
</body>
</html>
```